Tellmora Corporate Stationery

Look for design of all new corporate stationery for an existing insurance broking business that is going through a redesign and move from older partners to younger family members. New Logo is attached. Company is Brisbane based.
Colours in the Logo is Hex #43bed8 and website features a lot of hex #17b8d8. Website front page "A plan to protect you" - headline. "Professional and Individual advice to protect your greatest assets" - tagline.

Stationery required: Business Cards, Letter head, Thank-you cards, Birthday cards, Presentation folders, With Compliment slips and a powerpoint template. We also would like to send a card to all customers with the something along of the lines of "something new".

Target Market(s)

Customers of Insurance business looking at superannuation, life and income protection insurance, investment advice and wills

Industry/Entity Type

Insurance Broker

Font styles to use
Other font styles liked:
• same as logo

Requirements
Must have
• The above designs for new stationery for the new business including:
• Business Cards, Letter head, Thank-you cards, Birthday cards, Presentation folders, With Compliment slips and a powerpoint template. We also would like to send a card to all customers with the something along of the lines of "something new".
Nice to have
• It is a new look - long time family business being passed to next generation - big focus on advice for YOU, individual advice etc..

```html
<!DOCTYPE html>
<html lang="en">
<head>
<meta charset="utf-8">
<title>Tellmora Business Card</title>
<link href="https://fonts.googleapis.com/css2?family=Open+Sans:wght@400;600&display=swap" rel="stylesheet">
<style>
  :root {
    --page-bg: #e9e7e4;
    --teal: #17b8d8;
    --teal-deep: #1a9fb9;
    --panel-dark: #4b5055;
    --panel-light: #dfe3e6;
    --text-light: #f2f4f5;
    --text-dark: #1f2a30;
  }
  * { margin: 0; padding: 0; box-sizing: border-box; }
  html, body {
    width: 1200px; height: 969px; overflow: hidden;
    background: var(--page-bg);
    font-family: "Open Sans", Arial, sans-serif;
  }
  .business-card {
    position: absolute; left: 120px; top: 212px;
    width: 960px; height: 545px;
    border-radius: 28px; overflow: hidden;
    box-shadow: 0 14px 40px rgba(0,0,0,0.18);
  }
  .card-art { position: absolute; inset: 0; }
  .contact-block {
    position: absolute; left: 42px; top: 104px;
    color: var(--text-light);
  }
  .holder-name {
    font-size: 31px; font-weight: 600; color: var(--teal);
    letter-spacing: 0.5px; line-height: 1.2;
  }
  .holder-role { font-size: 24px; line-height: 1.3; margin-bottom: 22px; }
  .address { font-size: 23px; line-height: 33px; margin-bottom: 14px; }
  .contact-list { list-style: none; font-size: 23px; }
  .contact-list li { display: flex; align-items: center; height: 36.5px; }
  .contact-icon { width: 22px; height: 22px; margin-right: 18px; fill: var(--teal); flex: none; }
  .brand {
    position: absolute; left: 604px; top: 244px;
    display: flex; align-items: center; gap: 16px;
  }
  .brand-dot { width: 30px; height: 30px; border-radius: 50%; background: var(--teal); }
  .brand-name {
    font-size: 46px; font-weight: 600; color: var(--teal);
    letter-spacing: 2px; line-height: 1;
  }
</style>
</head>
<body>
  <div class="business-card">
    <svg class="card-art" width="960" height="545" viewBox="0 0 960 545">
      <defs>
        <linearGradient id="darkPanel" x1="0" y1="0" x2="1" y2="1">
          <stop offset="0" stop-color="#575c61"/>
          <stop offset="1" stop-color="#3f4449"/>
        </linearGradient>
        <radialGradient id="lightPanel" cx="0.5" cy="0.5" r="0.6">
          <stop offset="0" stop-color="#eef1f3"/>
          <stop offset="1" stop-color="#cdd3d7"/>
        </radialGradient>
      </defs>
      <rect width="960" height="545" fill="url(#darkPanel)"/>
      <circle cx="730" cy="275" r="320" fill="url(#lightPanel)"/>
      <rect x="730" y="0" width="230" height="545" fill="#d6dbde"/>
      <circle cx="730" cy="275" r="320" fill="url(#lightPanel)"/>
      <path d="M 560 0 A 320 320 0 0 0 560 545" fill="none" stroke="var(--teal)" stroke-width="7"/>
      <path d="M 600 0 A 290 290 0 0 0 600 545" fill="none" stroke="var(--teal)" stroke-opacity="0.25" stroke-width="3"/>
    </svg>

    <div class="contact-block">
      <p class="holder-name">DANIEL HARLOW</p>
      <p class="holder-role">CEO/FOUNDER</p>
      <p class="address">214 Wattle Grove<br>Brisbane, Queensland 4000</p>
      <ul class="contact-list">
        <li><svg class="contact-icon" viewBox="0 0 24 24"><path d="M6.6 10.8a15 15 0 0 0 6.6 6.6l2.2-2.2c.3-.3.7-.4 1-.2 1.1.4 2.3.6 3.6.6.6 0 1 .4 1 1V20c0 .6-.4 1-1 1A17 17 0 0 1 3 4c0-.6.4-1 1-1h3.5c.6 0 1 .4 1 1 0 1.3.2 2.5.6 3.6.1.3 0 .7-.2 1z"/></svg>612 408 3391</li>
        <li><svg class="contact-icon" viewBox="0 0 24 24"><path d="M7 1h10a2 2 0 0 1 2 2v18a2 2 0 0 1-2 2H7a2 2 0 0 1-2-2V3a2 2 0 0 1 2-2zm0 3v14h10V4zm5 15.5a1 1 0 1 0 0 2 1 1 0 0 0 0-2z"/></svg>614 552 7086</li>
        <li><svg class="contact-icon" viewBox="0 0 24 24"><path d="M6 2h9v5H6zM3 8h18a1 1 0 0 1 1 1v11a1 1 0 0 1-1 1H3a1 1 0 0 1-1-1V9a1 1 0 0 1 1-1zm3 4v2h2v-2zm4 0v2h2v-2zm4 0v2h2v-2zm-8 4v2h2v-2zm4 0v2h2v-2zm4 0v2h2v-2z"/></svg>612 408 3392</li>
        <li><svg class="contact-icon" viewBox="0 0 24 24"><path d="M2 5h20v14H2zm2 2v.5l8 5 8-5V7z"/></svg>hello@tellmora.com</li>
        <li><svg class="contact-icon" viewBox="0 0 24 24"><path d="M12 2a10 10 0 1 0 0 20 10 10 0 0 0 0-20zm-1 17.9A8 8 0 0 1 4.2 10L9 15v1a2 2 0 0 0 2 2zm6.9-2.5A2 2 0 0 0 16 16h-1v-3a1 1 0 0 0-1-1H8v-2h2a1 1 0 0 0 1-1V7h2a2 2 0 0 0 2-2v-.4a8 8 0 0 1 2.9 12.8z"/></svg>www.tellmora.com</li>
      </ul>
    </div>

    <div class="brand">
      <span class="brand-dot"></span>
      <span class="brand-name">TELLMORA</span>
    </div>
  </div>
</body>
</html>
```